Etiketten für Bio Seifen
Zielgruppe
Wir stellen hochwertig 'handgemachte' Bio-Seifen her. Die Zielgruppe ist von 3-99 Jahren und zusätzlich haben wir auch noch Seife für Hunde.
Der Firmenname ist 'Verdolina'
Aufgabenstellung
Das Etikett soll Bezug auf Natur, Bio, Nachhaltigkeit nehmen. Wir stellen uns 'weiche' Aquarellfarben vor...Seife: Lavendel, Calendular, 7 Kräuter etc.
Das Etikett soll auf eine Beutelschachtel. Die Schachtel hat eine Anmaße: Breite 55mm; Höhe 120mm; Tiefe 30mm
Das Etikett soll im vorderen- und hinteren Bereich zusammenhängend geklebt werden.
Das Etikett soll eine Abmaße von: Breite 51mm; Höhe 114mm haben (Vorderseite) Rückseite gleich.
Wir möchten die Produkte auch gerne nummerieren, d.h. jede Seife hat eine Nummer die nicht zu groß dargestellt werden soll aber trotzdem gut leserlich.
Wir haben noch ein paar Bilder hochgeladen wie wir uns das ungefähr vorstellen.

```html
<!DOCTYPE html>
<html lang="de">
<head>
<meta charset="UTF-8">
<title>Verdolina – Lavendel Seifenetikett</title>
<link href="https://fonts.googleapis.com/css2?family=Old+Standard+TT:wght@400;700&family=Playfair+Display:ital,wght@1,700&display=swap" rel="stylesheet">
<style>
  :root {
    --page-bg: #efedf2;
    --lavender-light: #ddd3ec;
    --lavender-mid: #b9a6dc;
    --lavender-deep: #7b5cc4;
    --purple: #5a1c7c;
    --white: #ffffff;
    --text-grey: #3c3c3c;
    --leaf-green: #d9efc8;
    --seal-green: #5fae4e;
  }
  * { box-sizing: border-box; margin: 0; padding: 0; }
  html, body {
    width: 1200px;
    height: 848px;
    overflow: hidden;
    background: var(--page-bg);
  }
  .canvas {
    position: relative;
    width: 1200px;
    height: 848px;
  }
  .label {
    position: absolute;
    left: 425px;
    top: 29px;
    width: 350px;
    height: 790px;
    overflow: hidden;
  }
  .label__pattern {
    position: absolute;
    inset: 0;
    background:
      radial-gradient(circle at 15% 20%, var(--lavender-mid) 0, transparent 22%),
      radial-gradient(circle at 85% 45%, var(--lavender-mid) 0, transparent 24%),
      radial-gradient(circle at 20% 80%, var(--lavender-mid) 0, transparent 22%),
      radial-gradient(circle at 80% 92%, var(--lavender-mid) 0, transparent 20%),
      var(--lavender-light);
  }
  .label__panel {
    position: absolute;
    left: 34px;
    right: 34px;
    top: 58px;
    bottom: 86px;
    background: var(--white);
    border: 6px solid var(--purple);
  }
  .label__panel::before {
    content: "";
    position: absolute;
    inset: 5px;
    border: 1.5px solid var(--purple);
  }
  .brand {
    position: absolute;
    top: 52px;
    left: 0;
    right: 0;
    text-align: center;
  }
  .brand__row {
    display: inline-flex;
    align-items: center;
    gap: 8px;
  }
  .brand__dot {
    width: 22px;
    height: 22px;
    border-radius: 50%;
    background: var(--leaf-green);
  }
  .brand__name {
    font-family: "Old Standard TT", serif;
    font-weight: 700;
    font-size: 19px;
    letter-spacing: 1px;
    color: var(--text-grey);
    text-transform: uppercase;
  }
  .brand__tagline {
    margin-top: 3px;
    font-family: "Old Standard TT", serif;
    font-size: 7px;
    letter-spacing: 1px;
    color: var(--text-grey);
  }
  .product-name {
    position: absolute;
    top: 168px;
    left: 0;
    right: 0;
    text-align: center;
    font-family: "Playfair Display", serif;
    font-style: italic;
    font-weight: 700;
    font-size: 48px;
    letter-spacing: -1px;
    color: var(--purple);
  }
  .sprig {
    position: absolute;
    top: 236px;
    left: 60px;
    right: 40px;
    height: 26px;
    border-radius: 13px;
    background: linear-gradient(90deg, #a6d08f 0%, var(--lavender-deep) 45%, var(--lavender-mid) 100%);
    opacity: 0.75;
  }
  .product-facts {
    position: absolute;
    top: 300px;
    left: 0;
    right: 0;
    text-align: center;
    font-family: "Old Standard TT", serif;
    font-size: 21px;
    line-height: 1.55;
    color: var(--text-grey);
    list-style: none;
  }
  .seal {
    position: absolute;
    top: 420px;
    left: 50%;
    width: 48px;
    height: 48px;
    margin-left: -24px;
    border-radius: 50%;
    background: var(--seal-green);
  }
  .number-tab {
    position: absolute;
    left: 145px;
    top: 580px;
    width: 46px;
    height: 130px;
    background: var(--purple);
    display: flex;
    align-items: flex-end;
    justify-content: center;
    padding-bottom: 6px;
    font-family: "Old Standard TT", serif;
    font-size: 30px;
    font-weight: 700;
    color: var(--white);
  }
</style>
</head>
<body>
  <main class="canvas">
    <section class="label" aria-label="Etikett Lavendel-Seife">
      <div class="label__pattern" role="img" aria-label="Aquarell-Lavendelblüten als Rahmenmuster"></div>
      <div class="label__panel">
        <div class="brand">
          <div class="brand__row">
            <span class="brand__dot"></span>
            <span class="brand__name">Verdolina</span>
          </div>
          <p class="brand__tagline">KÖRPER | GEIST | SEELE</p>
        </div>
        <h1 class="product-name">LAVENDEL</h1>
        <div class="sprig" role="img" aria-label="Aquarell-Lavendelzweig"></div>
        <ul class="product-facts">
          <li>SEIFE</li>
          <li>100% NATUR</li>
          <li>HANDMADE</li>
        </ul>
        <div class="seal" aria-label="Bio-Zertifikat"></div>
      </div>
      <div class="number-tab">1</div>
    </section>
  </main>
</body>
</html>
```